TWPC Business Card Design

Business card for sole operator professional civil and traffic engineer.
Clients are developers and planners who require assistance with traffic strategic master planning advice and design development for access and infrastructure associated with the development.
Colours already in use are greens for the business name and black for other legend. The attached file shows the letterhead template which is currently in use.
Target Market(s)
Professional Clients in development industry
Most clients known to the Principal and card is mostly required to allow ongoing contact
Industry/Entity Type
Business
Contact Information for Business Card
LACHLAN PETTIGREW CONSULTING PARTNERS
ABN 37 814 529 106
PO Box 418 KELWOOD NSW 2619
Lachlan Pettigrew 0412 358 971
l.pettigrew@corvanmail.net

```html
<!DOCTYPE html>
<html lang="en">
<head>
<meta charset="utf-8">
<title>TWPC Business Card</title>
<link rel="stylesheet" href="https://fonts.googleapis.com/css2?family=Arimo:wght@400&display=swap">
<style>
  :root {
    --brand-green: #8cc63f;
    --ink-black: #0a0a0a;
    --paper-white: #ffffff;
    --backdrop: #e9e7e3;
  }
  html, body {
    margin: 0;
    width: 1200px;
    height: 800px;
    overflow: hidden;
    background: var(--backdrop);
    font-family: "Arimo", Arial, sans-serif;
  }
  .card {
    position: absolute;
    left: 75px;
    top: 79px;
    width: 1050px;
    height: 642px;
    background: var(--ink-black);
    overflow: hidden;
    box-shadow: 0 10px 30px rgba(0,0,0,0.18);
  }
  .card-wave {
    position: absolute;
    inset: 0;
  }
  .business-name {
    position: absolute;
    right: 40px;
    top: 62px;
    margin: 0;
    font-size: 35px;
    font-weight: 400;
    letter-spacing: 0.5px;
    color: var(--brand-green);
    white-space: nowrap;
  }
  .abn {
    position: absolute;
    left: 560px;
    top: 118px;
    margin: 0;
    font-size: 22px;
    color: var(--ink-black);
    white-space: nowrap;
  }
  .contact-list {
    position: absolute;
    right: 40px;
    top: 238px;
    margin: 0;
    padding: 0;
    list-style: none;
    text-align: right;
  }
  .contact-item {
    display: flex;
    justify-content: flex-end;
    align-items: center;
    gap: 18px;
    height: 40px;
    font-size: 22px;
    color: var(--ink-black);
    white-space: nowrap;
  }
  .contact-icon {
    width: 24px;
    height: 24px;
    flex: none;
  }
  .principal-name {
    position: absolute;
    right: 90px;
    bottom: 52px;
    margin: 0;
    font-size: 28px;
    font-weight: 400;
    color: var(--brand-green);
    white-space: nowrap;
  }
</style>
</head>
<body>
  <article class="card">
    <svg class="card-wave" width="1050" height="642" viewBox="0 0 1050 642">
      <path d="M0,0 H1050 V560 C900,470 650,440 430,445 C260,450 170,420 155,320 C140,200 120,90 0,60 Z"
            fill="none" stroke="var(--brand-green)" stroke-width="22"/>
      <path d="M0,0 H1050 V560 C900,470 650,440 430,445 C260,450 170,420 155,320 C140,200 120,90 0,60 Z"
            fill="var(--paper-white)"/>
    </svg>

    <h1 class="business-name">LACHLAN PETTIGREW CONSULTING PARTNERS</h1>
    <p class="abn">ABN 37 814 529 106</p>

    <ul class="contact-list">
      <li class="contact-item">
        <span>l.pettigrew@corvanmail.net</span>
        <span class="contact-icon"></span>
      </li>
      <li class="contact-item">
        <span>0412 358 971</span>
        <svg class="contact-icon" viewBox="0 0 24 24" aria-label="Phone">
          <path d="M3 9 C6 4 18 4 21 9 L18 11 L16 8 H8 L6 11 Z" fill="var(--brand-green)"/>
          <path d="M6 12 H18 L20 20 H4 Z" fill="var(--brand-green)"/>
          <circle cx="12" cy="16" r="2.5" fill="var(--paper-white)"/>
        </svg>
      </li>
      <li class="contact-item">
        <span>418 KELWOOD NSW 2619</span>
        <svg class="contact-icon" viewBox="0 0 24 24" aria-label="Email">
          <rect x="2" y="5" width="20" height="14" fill="var(--brand-green)"/>
          <path d="M2 5 L12 13 L22 5" fill="none" stroke="var(--paper-white)" stroke-width="1.6"/>
        </svg>
      </li>
      <li class="contact-item">
        <span></span>
        <svg class="contact-icon" viewBox="0 0 24 24" aria-label="Location">
          <path d="M12 2 C7.5 2 5 5.5 5 9 C5 14 12 22 12 22 C12 22 19 14 19 9 C19 5.5 16.5 2 12 2 Z" fill="var(--brand-green)"/>
          <circle cx="12" cy="9" r="2.8" fill="var(--paper-white)"/>
        </svg>
      </li>
    </ul>

    <h2 class="principal-name">LACHLAN PETTIGREW</h2>
  </article>
</body>
</html>
```